TA BRAMLEY BUSINESS CARD DESIGN PROJECT

We need to utilize our logo that was expertly created on PixelHarbor and now need to match this with a business card design.

```html
<!DOCTYPE html>
<html lang="en">
<head>
<meta charset="utf-8">
<title>TA BRAMLEY Business Card</title>
<link href="https://fonts.googleapis.com/css2?family=Montserrat:wght@400;700&family=Open+Sans:wght@400&display=swap" rel="stylesheet">
<style>
  :root {
    --brand-blue: #1059ab;
    --ink-black: #1a1a1a;
    --paper-white: #ffffff;
    --stage-grey: #d9d9d6;
    --muted-text: #222222;
  }
  * { margin: 0; padding: 0; box-sizing: border-box; }
  html, body { width: 1200px; height: 801px; overflow: hidden; }
  body {
    background: var(--stage-grey);
    font-family: "Open Sans", Arial, sans-serif;
    position: relative;
  }
  .card {
    position: absolute;
    top: 246px;
    width: 540px;
    height: 308px;
    overflow: hidden;
    box-shadow: 0 6px 18px rgba(0,0,0,0.18);
  }
  .card-front { left: 30px; background: var(--paper-white); }
  .card-back { left: 630px; background: var(--brand-blue); display: flex; align-items: center; justify-content: center; }

  .front-shapes { position: absolute; inset: 0; }

  .brand-name {
    font-family: "Montserrat", Arial, sans-serif;
    font-weight: 700;
    letter-spacing: 0.06em;
    display: flex;
    align-items: center;
  }
  .brand-mark-square { display: inline-block; }
  .card-front .brand-name {
    position: absolute;
    left: 34px;
    top: 62px;
    font-size: 30px;
    color: var(--brand-blue);
    gap: 10px;
  }
  .card-front .brand-mark-square { width: 18px; height: 18px; background: var(--brand-blue); }

  .card-back .brand-name { font-size: 58px; color: var(--paper-white); gap: 18px; }
  .card-back .brand-mark-square { width: 34px; height: 34px; background: var(--paper-white); }

  .holder {
    position: absolute;
    right: 46px;
    top: 24px;
    text-align: left;
  }
  .holder-name {
    font-family: "Montserrat", Arial, sans-serif;
    font-weight: 700;
    font-size: 20px;
    color: var(--brand-blue);
    letter-spacing: 0.02em;
  }
  .holder-title {
    font-family: "Montserrat", Arial, sans-serif;
    font-size: 14px;
    color: var(--muted-text);
    margin-top: 2px;
  }
  .title-bar {
    position: absolute;
    right: 0;
    top: 26px;
    width: 12px;
    height: 40px;
    background: var(--brand-blue);
  }

  .contact-list {
    position: absolute;
    left: 34px;
    bottom: 18px;
    list-style: none;
    color: var(--paper-white);
    font-size: 13px;
    line-height: 21px;
  }
  .contact-list li { display: flex; align-items: center; gap: 10px; }
  .contact-icon { width: 12px; height: 12px; flex: none; }

  .address {
    position: absolute;
    right: 28px;
    top: 168px;
    color: var(--paper-white);
    font-size: 13px;
    line-height: 19px;
    text-align: center;
  }
</style>
</head>
<body>

<section class="card card-front" aria-label="Business card front">
  <svg class="front-shapes" width="540" height="308" viewBox="0 0 540 308" aria-hidden="true">
    <path d="M14 192 C 190 150 370 88 540 70 L540 84 C 370 100 190 158 14 192 Z" fill="var(--brand-blue)"/>
    <path d="M0 204 C 190 166 370 104 540 92 L540 308 L0 308 Z" fill="var(--ink-black)"/>
  </svg>

  <div class="brand-name"><span class="brand-mark-square"></span>TA BRAMLEY</div>

  <div class="holder">
    <div class="holder-name">MARCUS HALE</div>
    <div class="holder-title">Managing Director</div>
  </div>
  <div class="title-bar"></div>

  <ul class="contact-list">
    <li>
      <svg class="contact-icon" viewBox="0 0 12 12"><path d="M2 1 L4.5 1 L5.2 3.6 L3.8 4.6 C4.5 6 6 7.5 7.4 8.2 L8.4 6.8 L11 7.5 L11 10 C11 10.6 10.6 11 10 11 C5 11 1 7 1 2 C1 1.4 1.4 1 2 1 Z" fill="var(--brand-blue)"/></svg>
      2233333333
    </li>
    <li>
      <svg class="contact-icon" viewBox="0 0 12 12"><rect x="2.5" y="0.8" width="7" height="10.4" rx="1" fill="none" stroke="var(--brand-blue)" stroke-width="1.3"/><circle cx="6" cy="9.4" r="0.7" fill="var(--brand-blue)"/></svg>
      00000000000
    </li>
    <li>
      <svg class="contact-icon" viewBox="0 0 12 12"><rect x="0.5" y="2" width="11" height="8" fill="var(--brand-blue)"/><path d="M0.5 2 L6 6.5 L11.5 2" fill="none" stroke="var(--ink-black)" stroke-width="1"/></svg>
      info@bramleymail.com
    </li>
    <li>
      <svg class="contact-icon" viewBox="0 0 12 12"><circle cx="6" cy="6" r="5.3" fill="none" stroke="var(--brand-blue)" stroke-width="1.2"/><path d="M0.8 6 H11.2 M6 0.8 C3.5 3.5 3.5 8.5 6 11.2 M6 0.8 C8.5 3.5 8.5 8.5 6 11.2" fill="none" stroke="var(--brand-blue)" stroke-width="1"/></svg>
      www.yourwebsite.com
    </li>
  </ul>

  <address class="address" style="font-style: normal;">
    Your address, City<br>State, Zip 1234
  </address>
</section>

<section class="card card-back" aria-label="Business card back">
  <div class="brand-name"><span class="brand-mark-square"></span>TA BRAMLEY</div>
</section>

</body>
</html>
```